Drifting Lantern Coffee Co menu

We would like our existing menu tidied up.
we want to keep the all the items, but need it less busy and clearer to read.

Also want to leave a bit of space to add a few item in the future.

```html
<!DOCTYPE html>
<html lang="en">
<head>
<meta charset="utf-8">
<title>Drifting Lantern Coffee Co — Menu</title>
<link href="https://fonts.googleapis.com/css2?family=Rye&family=Arimo:wght@400;700&display=swap" rel="stylesheet">
<style>
  :root {
    --teal: #3a8b96;
    --ink: #2e2e2e;
    --rule: #3a3a3a;
    --paper: #ffffff;
    --backdrop: #eaeaea;
    --leaf: #e6eef0;
  }
  * { box-sizing: border-box; margin: 0; padding: 0; }
  html, body { width: 1200px; height: 960px; overflow: hidden; }
  body {
    background: var(--backdrop);
    font-family: "Arimo", Arial, sans-serif;
    color: var(--ink);
    display: flex; align-items: center; justify-content: center;
  }
  .menu-page {
    position: relative;
    width: 640px; height: 905px;
    background: var(--paper);
    padding: 34px 44px 40px;
    box-shadow: 0 4px 18px rgba(0,0,0,.12);
  }
  .leaf-motif {
    position: absolute; left: 150px; top: 110px;
    width: 300px; height: 380px;
    pointer-events: none;
  }
  .top-grid, .specialty { position: relative; }
  .top-grid {
    display: grid; grid-template-columns: 1fr 1fr; column-gap: 36px;
  }
  .brand {
    height: 92px; display: flex; align-items: center; gap: 10px;
    border-bottom: 1.5px solid var(--rule);
    font-weight: 700; font-size: 19px; line-height: 1.15; color: var(--teal);
  }
  .brand-dot { width: 14px; height: 14px; border-radius: 50%; background: var(--teal); flex: none; }
  .page-title {
    font-family: "Rye", serif; color: var(--teal);
    height: 92px; display: flex; flex-direction: column; justify-content: center; align-items: center;
    border-bottom: 1.5px solid var(--rule);
  }
  .page-title .main { font-size: 44px; line-height: 1; letter-spacing: 1px; }
  .page-title .sub { font-size: 15px; color: var(--ink); margin-top: 2px; }
  .section-label {
    display: inline-block; margin: 22px 0 8px;
    font-weight: 700; font-size: 14px; color: var(--teal);
    text-decoration: underline;
  }
  .item { margin-bottom: 11px; }
  .item-head { display: flex; justify-content: space-between; align-items: baseline; }
  .item-name { font-weight: 700; font-size: 15px; color: var(--teal); }
  .item-price { font-weight: 700; font-size: 11px; color: var(--teal); }
  .item-desc { font-size: 9.5px; line-height: 1.35; color: var(--ink); }
  .split { border-top: 1.5px solid var(--rule); margin-top: 14px; padding-top: 6px; }
  .specialty {
    margin-top: 20px; border-top: 1.5px solid var(--rule);
    text-align: center; padding-top: 16px;
  }
  .specialty-title { font-family: "Rye", serif; color: var(--teal); font-size: 30px; margin-bottom: 14px; }
  .feature { margin: 0 auto 18px; max-width: 470px; }
  .feature .item-name { display: block; font-size: 16px; margin-bottom: 4px; }
  .feature .item-price { display: block; margin-top: 5px; font-size: 12px; }
  .end-rule { border-top: 1.5px solid var(--rule); margin-top: 36px; }
</style>
</head>
<body>
  <main class="menu-page">
    <svg class="leaf-motif" viewBox="0 0 300 380" role="img" aria-label="Faint leaf decoration behind the menu items">
      <ellipse cx="150" cy="190" rx="140" ry="180" fill="var(--leaf)" opacity=".6"/>
    </svg>

    <div class="top-grid">
      <section class="col-coffee">
        <header class="brand"><span class="brand-dot"></span><span>Drifting Lantern<br>Coffee Co</span></header>
        <h2 class="section-label">Coffee</h2>
        <div class="item"><div class="item-head"><span class="item-name">Flat White</span><span class="item-price">$5.00</span></div>
          <p class="item-desc">Espresso Shot With A Steamed Milk.<br>Small $5 - Medium $6 - Large $7</p></div>
        <div class="item"><div class="item-head"><span class="item-name">Cappuccino</span><span class="item-price">$5.00</span></div>
          <p class="item-desc">Espresso Shot With Steamed Milk, A Thick Layer Of Milk Foam And Chocolate Powder Topping.<br>Small $5 - Medium $6 - Large $7</p></div>
        <div class="item"><div class="item-head"><span class="item-name">Latte</span><span class="item-price">$5.00</span></div>
          <p class="item-desc">Espresso Shot With Steamed Milk And A Thin Layer Of Milk Foam<br>Small $5 - Medium $6 - Large $7</p></div>
        <div class="item"><div class="item-head"><span class="item-name">Mocha</span><span class="item-price">$5.50</span></div>
          <p class="item-desc">Espresso Shot, Belgian Chocolate Raw Natural Infusion With A Medium Layer Of Milk Foam.<br>Small $5 - Medium $6 - Large $7</p></div>
        <div class="item"><div class="item-head"><span class="item-name">Americano</span><span class="item-price">$5.00</span></div>
          <p class="item-desc">Americano - Espresso Shot Topped Up With Hot Water. Long Black - Hot Water Topped Off With Espresso Shot<br>Small $5 - Medium $6 - Large $7</p></div>
        <div class="item"><div class="item-head"><span class="item-name">Espresso</span><span class="item-price">$3.00</span></div>
          <p class="item-desc">Double Espresso Shot</p></div>
        <div class="item"><div class="item-head"><span class="item-name">Filter / Batch Brew Coffee</span><span class="item-price">$4.00</span></div>
          <p class="item-desc">Small $4 - Medium $4 - Large $4</p></div>
      </section>

      <section class="col-tea">
        <header class="page-title"><span class="main">COFFEE</span><span class="sub">&amp; TEA</span></header>
        <h2 class="section-label">Tea / Other drinks</h2>
        <div class="item"><div class="item-head"><span class="item-name">Organic Green Tea</span><span class="item-price">$5.00</span></div>
          <p class="item-desc">Small $5 - Medium $6 - Large $7</p></div>
        <div class="item"><div class="item-head"><span class="item-name">English Breakfast Tea</span><span class="item-price">$5.00</span></div>
          <p class="item-desc">Small $5 - Medium $6 - Large $7</p></div>
        <div class="item"><div class="item-head"><span class="item-name">Organic Earl Grey Tea</span><span class="item-price">$5.00</span></div>
          <p class="item-desc">Small $5 - Medium $6 - Large $7</p></div>
        <div class="item"><div class="item-head"><span class="item-name">Hot Chocolate</span><span class="item-price">$5.00</span></div>
          <p class="item-desc">Small $5 - Medium $6 - Large $7</p></div>
        <div class="item"><div class="item-head"><span class="item-name">Dark Cacoa Hot Chocolate</span><span class="item-price">$5.00</span></div>
          <p class="item-desc">Small $5 - Medium $6 - Large $7</p></div>
        <div class="item"><div class="item-head"><span class="item-name">Chai Latte</span><span class="item-price">$5.00</span></div>
          <p class="item-desc">Small $5 - Medium $6 - Large $7</p></div>
        <div class="split">
          <div class="item"><div class="item-head"><span class="item-name">Wild Natural Infusions</span><span class="item-price">$0.50</span></div>
            <p class="item-desc">Caramel, Vanilla, Chai Spice,<br>Hazelnut, Belgian Chocolate</p></div>
          <div class="item"><div class="item-head"><span class="item-name">Milks</span><span class="item-price">$INC</span></div>
            <p class="item-desc">Full Cream, Skinny, Oat,<br>Almond, Soy</p></div>
        </div>
      </section>
    </div>

    <section class="specialty">
      <h2 class="specialty-title">SPECIALTY DRINKS</h2>
      <div class="feature">
        <span class="item-name">Honey Brewed Chai</span>
        <p class="item-desc">Our Honey Chai Is Handmade And Blended In Western Australia. It Is Made From The Finest Black Tea Leaves Available, Aromatic Freshly Ground Spices And Infused With Locally Sourced Raw Honey. Served With A Choice Of Steamed Milk.</p>
        <span class="item-price">$7.00</span>
      </div>
      <div class="feature">
        <span class="item-name">Colombian Cacoa Salted Caramel Hot Chocolate</span>
        <p class="item-desc">Made With Deep Toned And Rich Cocoa Sourced From Ancient Cocao Growing Regions Of Colombia And Sweetened With Just Enough Organic Unrefined Colombian Panela, All Balanced Perfectly With A Caramel Raw Natural Infusion And Pink Himalayan Rock Salt. Served With A Choice Of Steamed Milk.</p>
        <span class="item-price">$7.00</span>
      </div>
      <div class="end-rule"></div>
    </section>
  </main>
</body>
</html>
```